Awesome photographers card for an awesome new business

Double sided business card Black background and silver logo in middle on one side. Details on otherside. please keep it simple

Industry/Entity Type

Photographer

Contact Information for Business Card

Gerald Fenwick
0452817360
GeraldFenwickPhotography47@mailbox.test
www.GeraldFenwickPhotography.test.au
Instagram _Gerald_fenwick

Requirements
Must have
• My logo in Silver
• please use instagram logo instead of "Instagram"

```html
<!DOCTYPE html>
<html lang="en">
<head>
<meta charset="utf-8">
<title>Gerald Fenwick Photography – Business Card</title>
<link rel="stylesheet" href="https://fonts.googleapis.com/css2?family=Questrial&display=swap">
<style>
  :root {
    --backdrop: #b9b9b9;
    --card-front: #f7f7f7;
    --card-back: #151515;
    --ink-name: #555555;
    --ink-details: #474747;
    --rule: #8a8a8a;
    --silver: #c9c9c9;
  }
  * { margin: 0; padding: 0; box-sizing: border-box; }
  html, body {
    width: 1200px;
    height: 960px;
    overflow: hidden;
    background: var(--backdrop);
    font-family: "Questrial", "Century Gothic", sans-serif;
  }
  .canvas {
    position: relative;
    width: 1200px;
    height: 960px;
  }
  .card {
    position: absolute;
    width: 600px;
    height: 342px;
    border-radius: 18px;
  }
  .card--front {
    left: 322px;
    top: 126px;
    background: var(--card-front);
    text-align: center;
  }
  .card--back {
    left: 320px;
    top: 501px;
    background: var(--card-back);
    display: flex;
    align-items: center;
    justify-content: center;
  }
  .holder-name {
    position: absolute;
    left: 0;
    right: 0;
    top: 116px;
    font-size: 23px;
    font-weight: 400;
    letter-spacing: 0.2px;
    color: var(--ink-name);
    -webkit-text-stroke: 0.5px var(--ink-name);
    text-transform: uppercase;
  }
  .holder-rule {
    position: absolute;
    left: 277px;
    top: 149px;
    width: 46px;
    height: 1px;
    background: var(--rule);
  }
  .contact-list {
    position: absolute;
    left: 0;
    right: 0;
    top: 162px;
    list-style: none;
    font-size: 14px;
    line-height: 18px;
    color: var(--ink-details);
  }
  .brand-mark {
    display: flex;
    align-items: center;
    gap: 14px;
  }
  .brand-dot {
    width: 14px;
    height: 14px;
    border-radius: 50%;
    background: var(--silver);
  }
  .brand-name {
    font-size: 26px;
    letter-spacing: 4px;
    text-transform: uppercase;
    color: var(--silver);
  }
</style>
</head>
<body>
<main class="canvas">
  <section class="card card--front" aria-label="Business card, details side">
    <h1 class="holder-name">Gerald Fenwick</h1>
    <div class="holder-rule"></div>
    <ul class="contact-list">
      <li>Phone 0452817360</li>
      <li>GeraldFenwickPhotography47@mailbox.test</li>
      <li>www.GeraldFenwickPhotography.test.au</li>
      <li>Instagram _Gerald_fenwick</li>
    </ul>
  </section>

  <section class="card card--back" aria-label="Business card, brand side">
    <div class="brand-mark">
      <span class="brand-dot"></span>
      <span class="brand-name">Gerald Fenwick</span>
    </div>
  </section>
</main>
</body>
</html>
```